Tradlo - Forex Signal Services Moments Matter Most. Reshape your path.

I need an attractive eye catching web design that is azure friendly. I currently have a web programmer working on the backend of my website. Now I need a professional design to attract and retain customers. This site needs to be mobile friendly.

Tradlo is a highly reputable, trustworthy and professional site that offers forex signals to traders in all parts of the globe. With accurate and reliable forex signals, traders can not only make money but also boost their profits.

At Tradlo, we want our clients to have complete faith on us and our services! We also do not want our users to lead a simple and monotonous life. Instead our goal is to help them create an extra source of steady income. However, this is possible only when our clients resolve to change their lives for the better. They need to change their mindset and most importantly develop a positive frame of mind. That’s exactly why at Tradlo, we provide our clients with innumerable personal development tools and resources that’ll aid them in changing all the aspects of their lives. We want our traders to feel inspired and educate them in the right way!

Colors are flexible.

I do like the simplicity of www.brightmarkvo.example.
I do want a design more professional in appearance and not everything on page one.

I have not been able to decide on a logo. There is one of lower quality as I have not paid for it yet but I will if you decide it's the best for my business I will. Or should one feel that they have a better idea for a logo, I will pay for it if i like it.

I have included some of the content of my site so you can get a feel for where I am coming from.
(Please note that this content is still in the editing process)
Updates

Project Deadline Extended Reason: My content was not complete nor finalization of the final logo. We will allow a few more days for designers to modify the website.Thank you for your patience and understanding. Added Tuesday, January 24, 2017

Target Market(s)

I work with Forex Traders, Investors wanting to control their own portfolios, and remote nomads/mellienials

Coding

Coded - Design and coding required

Number of Pages Required

5+ page

Requirements
Must have
• I must have a professional clean look. I want the site to be interactive and eye catching. I want my audience hooked within seconds of opening it. It has to have all important information first. Photos must be legit and not spammy. I work as a representative in the financial market. I want my site to reflect that I stand by my product and reputation means everything to me. This site has to be engaging.
• Sorry, I should have included this earlier of what I will all need on this site.
• I'll have about Tradlo (my company, what we stand for, who we work with, my strategy, etc....
• about me (why i started this company, who I am)
• Performance (graphs and recent posts of signals)
• Membership (how to sign up)
• Terms of service/legal/disclaimers
• FAQS
• Personal Development Resources
• Forex Education Resources
Nice to have
• Quick links to bounce around the site faster.
Should not have
• I do not want over the top white collar conservative.

```html
<!DOCTYPE html>
<html lang="en">
<head>
<meta charset="utf-8">
<title>Tradlo - Forex Signal Services</title>
<link rel="stylesheet" href="https://fonts.googleapis.com/css2?family=Roboto:wght@400;500;700&family=Open+Sans:wght@400;600&display=swap">
<style>
:root{
  --blue:#2a9fd8;
  --blue-band:#33a3d8;
  --ink:#3d3f44;
  --text:#6f7378;
  --muted:#9a9ea3;
  --line:#e3e5e8;
  --soft:#f4f5f7;
  --white:#ffffff;
  --hero-a:#b7c4cf;
  --hero-b:#e7ebee;
  --dark-a:#2a323a;
  --dark-b:#59626b;
}
*{box-sizing:border-box;margin:0;padding:0}
html,body{width:1200px;height:2951px;overflow:hidden;background:var(--white)}
body{position:relative;font-family:"Open Sans",Arial,sans-serif;color:var(--text)}
.abs{position:absolute}
h1,h2,h3,h4{font-family:"Roboto",Arial,sans-serif;font-weight:400;color:var(--ink)}
.accent{color:var(--blue)}

/* header */
.site-header{left:0;top:0;width:1200px;height:100px;background:var(--white);border-top:3px solid var(--blue)}
.brand{left:110px;top:22px;display:flex;align-items:center;gap:10px}
.brand-dot{width:26px;height:26px;border-radius:50%;background:var(--blue)}
.brand-name{font-family:"Roboto",sans-serif;font-size:28px;font-weight:500;color:var(--ink);letter-spacing:1px}
.main-nav a{position:absolute;top:44px;font-family:"Roboto",sans-serif;font-size:12px;font-weight:500;color:#555;text-decoration:none;letter-spacing:.3px}
.main-nav a.active{color:var(--blue)}

/* hero */
.hero{left:0;top:100px;width:1200px;height:525px;background:linear-gradient(180deg,var(--hero-a) 0%,var(--hero-b) 70%,#d9d6d0 100%)}
.hero-quote{left:0;top:150px;width:1200px;text-align:center;font-family:"Roboto",sans-serif;font-size:34px;color:var(--white);letter-spacing:.5px}
.hero-arrow{top:338px;width:50px;height:50px;border-radius:50%;border:2px solid var(--white);background:rgba(255,255,255,.15)}

/* welcome */
.welcome{left:0;top:625px;width:1200px;height:256px;background:#f8f9fa;border-bottom:1px solid var(--line);box-shadow:0 2px 4px rgba(0,0,0,.05)}
.section-title{width:1200px;left:0;text-align:center;font-size:30px}
.body-copy{font-size:11px;line-height:27px;color:var(--text)}
.centered{left:0;width:1200px;text-align:center}
.btn-outline{display:flex;align-items:center;justify-content:center;border:1.5px solid var(--blue);border-radius:24px;font-family:"Roboto",sans-serif;font-size:12px;font-weight:500;color:var(--blue);letter-spacing:.4px}
.btn-light{border-color:var(--white);color:var(--white)}

/* features */
.feature-icon{width:118px;height:118px;border-radius:50%;border:1px solid var(--line);background:var(--white);display:flex;align-items:center;justify-content:center}
.feature-title{width:300px;text-align:center;font-size:19px;color:var(--blue);font-weight:500}
.feature-copy{width:300px;text-align:center;font-size:11px;line-height:25px}

/* why */
.why{left:0;top:1220px;width:1200px;height:403px;background:linear-gradient(120deg,var(--dark-a) 0%,var(--dark-b) 55%,#3a434c 100%)}
.why-title{color:var(--white);font-size:27px}
.why-copy{color:#e9ecef}

/* philosophy */
.philosophy-title{left:87px;top:1682px;font-size:28px;font-weight:500}
.philosophy-copy{left:87px;width:520px;font-size:11px;line-height:25px}
.desktop-visual{left:669px;top:1652px;width:452px;height:394px;border-radius:8px;background:linear-gradient(160deg,#3c4146 0%,#1f2327 60%,#d7dadd 100%)}

/* faq & about */
.info-band{left:0;top:2087px;width:1200px;height:418px;background:var(--soft)}
.col-title{font-size:27px;font-weight:500}
.faq-q{left:87px;width:490px;font-family:"Roboto",sans-serif;font-size:16px;color:var(--ink)}
.faq-q b{font-size:22px;font-weight:500;color:var(--blue);margin-right:4px}
.faq-q.open{color:var(--blue)}
.faq-rule{left:87px;width:490px;height:1px;background:var(--line)}
.faq-answer{left:115px;width:460px;font-size:11px;line-height:24px}
.view-more{left:87px;top:2442px;font-family:"Roboto",sans-serif;font-size:12px;font-weight:500;color:var(--blue);display:flex;align-items:center;gap:6px;text-decoration:underline}
.about-copy{left:625px;top:2158px;width:495px;font-size:11px;line-height:24px}
.about-list{left:625px;top:2282px;list-style:none}
.about-list li{display:flex;align-items:center;gap:16px;height:36.5px;font-size:11px}

/* partners */
.partners{left:0;top:2505px;width:1200px;height:115px;background:var(--blue-band)}
.partner-badge{top:2526px;width:142px;height:74px;border:1px solid rgba(255,255,255,.55);display:flex;align-items:center;justify-content:center}
.partner-badge span{width:96px;height:22px;border-radius:3px;background:rgba(255,255,255,.85)}

/* footer */
.site-footer{left:0;top:2620px;width:1200px;height:331px;background:var(--soft)}
.footer-brand{left:150px;top:2720px;display:flex;flex-direction:column;align-items:center;gap:12px}
.footer-brand .brand-dot{width:40px;height:40px}
.footer-brand .brand-name{font-size:34px}
.footer-heading{font-size:15px;font-weight:500;letter-spacing:.5px;color:var(--ink)}
.contact-list{left:400px;top:2712px;list-style:none}
.contact-list li{display:flex;gap:14px;font-size:11px;line-height:18px;margin-bottom:11px;color:var(--text)}
.contact-list svg{flex:none;margin-top:2px}
.contact-list a{color:var(--text)}
.newsletter-copy{left:653px;top:2712px;width:220px;font-size:11px;line-height:19px}
.email-field{left:653px;top:2758px;width:213px;height:32px;background:var(--white);border:1px solid var(--line);font-size:11px;color:#777;padding:8px 14px}
.subscribe-btn{left:653px;top:2806px;width:82px;height:26px;background:var(--blue);color:var(--white);font-family:"Roboto",sans-serif;font-size:10px;font-weight:500;display:flex;align-items:center;justify-content:center}
.follow-copy{left:903px;top:2712px;width:210px;font-size:11px;line-height:19px}
.social-row{left:903px;top:2786px;display:flex;gap:10px}
.social-row span{width:34px;height:34px;border-radius:50%;border:1px solid #c6c9cd}
.footer-rule{left:0;top:2886px;width:1200px;height:1px;background:var(--line)}
.copyright{left:0;top:2910px;width:1200px;text-align:center;font-size:11px;color:var(--muted)}
</style>
</head>
<body>

<header class="site-header abs">
  <div class="brand abs"><span class="brand-dot"></span><span class="brand-name">Tradlo</span></div>
  <nav class="main-nav">
    <a class="active" style="left:449px">HOME</a>
    <a style="left:555px">ABOUT US</a>
    <a style="left:683px">SERVICES</a>
    <a style="left:808px">FEATURED</a>
    <a style="left:938px">NEWS</a>
    <a style="left:1043px">CONTACT US</a>
  </nav>
</header>

<section class="hero abs" role="img" aria-label="Laptop on a desk showing forex trading charts in front of a city skyline">
</section>
<p class="hero-quote abs">“MOMENTS MATTER MOST. RESHAPE YOUR PATH”</p>
<div class="hero-arrow abs" style="left:26px"><svg width="46" height="46" viewBox="0 0 46 46"><path d="M26 15 L18 23 L26 31" fill="none" stroke="#fff" stroke-width="2.5"/></svg></div>
<div class="hero-arrow abs" style="left:1123px"><svg width="46" height="46" viewBox="0 0 46 46"><path d="M20 15 L28 23 L20 31" fill="none" stroke="#fff" stroke-width="2.5"/></svg></div>

<section class="welcome abs"></section>
<h2 class="section-title abs" style="top:655px">Welcome to <span class="accent">Tradlo</span></h2>
<p class="body-copy abs centered" style="top:708px">Pardon my language but there is a lot of 'crap', on the internet, especially when it comes to the services I offer.&nbsp; I have spent countless hours and years<br>of my life towards my passion for the currency industry.&nbsp; I finally developed a strategy I am proud of and stand by my product with my name and company<br>that the extent of our personal success is a measure of accomplishments we have helped others create.</p>
<div class="btn-outline abs" style="left:476px;top:812px;width:248px;height:44px">CLICK HERE FOR MORE INFO</div>

<section class="features">
  <div class="feature-icon abs" style="left:193px;top:936px">
    <svg width="54" height="54" viewBox="0 0 54 54"><circle cx="27" cy="27" r="25" fill="var(--blue)"/><circle cx="27" cy="20" r="7" fill="#fff"/><path d="M13 42 C14 32 40 32 41 42 Z" fill="#fff"/><text x="27" y="24" text-anchor="middle" font-family="Roboto,sans-serif" font-size="10" font-weight="700" fill="var(--blue)">$</text></svg>
  </div>
  <div class="feature-icon abs" style="left:541px;top:936px">
    <svg width="54" height="54" viewBox="0 0 54 54"><path d="M27 12 a12 12 0 0 1 7 22 v5 h-14 v-5 a12 12 0 0 1 7 -22z" fill="var(--blue)"/><rect x="21" y="41" width="12" height="3" fill="var(--blue)"/><rect x="23" y="46" width="8" height="3" fill="var(--blue)"/><g stroke="var(--blue)" stroke-width="2"><line x1="27" y1="2" x2="27" y2="7"/><line x1="9" y1="10" x2="13" y2="14"/><line x1="45" y1="10" x2="41" y2="14"/><line x1="3" y1="25" x2="8" y2="25"/><line x1="51" y1="25" x2="46" y2="25"/></g></svg>
  </div>
  <div class="feature-icon abs" style="left:891px;top:936px">
    <svg width="54" height="54" viewBox="0 0 54 54"><path d="M20 8 h14 l-4 8 h-6z" fill="var(--blue)"/><path d="M22 17 h10 C46 24 48 48 27 48 C6 48 8 24 22 17z" fill="var(--blue)"/><text x="27" y="40" text-anchor="middle" font-family="Roboto,sans-serif" font-size="16" font-weight="700" fill="#fff">$</text></svg>
  </div>
  <h3 class="feature-title abs" style="left:102px;top:1068px">Investors</h3>
  <h3 class="feature-title abs" style="left:450px;top:1068px">Entrepreneurs</h3>
  <h3 class="feature-title abs" style="left:800px;top:1068px">Make Money</h3>
  <p class="feature-copy abs" style="left:102px;top:1104px">Work from home has become very popular over the years ever since the internetbecame available to more households around the world.</p>
  <p class="feature-copy abs" style="left:450px;top:1104px">Work from home has become very popular over the years ever since the internetbecame available to more households around the world.</p>
  <p class="feature-copy abs" style="left:800px;top:1104px">Work from home has become very popular over the years ever since the internetbecame available to more households around the world.</p>
</section>

<section class="why abs" role="img" aria-label="Hands reviewing printed financial charts on a desk"></section>
<h2 class="section-title why-title abs" style="top:1320px">Why Tradlo</h2>
<p class="body-copy why-copy abs centered" style="top:1376px">We're a small company based in the beautiful rockies, Ridgefall, Alberta, Canada with over 9 years of successful trading experience<br>in the foreign exchange market. We decided to launch our service for two reasons: learning to trade is a difficult process that&nbsp; signal<br>services that take advantage of these traders. Our aim is to help aspiring traders</p>
<div class="btn-outline btn-light abs" style="left:476px;top:1480px;width:248px;height:44px">CLICK HERE FOR MORE INFO</div>

<h2 class="philosophy-title abs">What is your trading <span class="accent">philosophy &amp; style?</span></h2>
<p class="philosophy-copy abs" style="top:1743px">We follow naked forex trading techniques including price action, immediate trend and personal-ized mathematical formulas. Our success stems from our strict enforcement of discipline, patie nce, attitude, economics and timing to help our traders maximize their gains from forex trading. Obviously we do not always win, but our winning trades</p>
<p class="philosophy-copy abs" style="top:1870px">Exceed those that are not and our take profit target is always bigger than our stop loss.We look at multiple time frames to qualify setups that define our trading edge. We pay close to the Lond on market and our entries are often based off of the 1-hour chart.</p>
<div class="btn-outline abs" style="left:87px;top:1983px;width:169px;height:44px">READ MORE INFO</div>
<div class="desktop-visual abs" role="img" aria-label="Desktop computer with keyboard and mouse showing the Tradlo home screen"></div>

<section class="info-band abs"></section>
<h2 class="col-title abs" style="left:87px;top:2106px">Our <span class="accent">Faq's</span></h2>
<p class="faq-q open abs" style="top:2170px"><b>Q.</b>We're a small company based in the beautiful rockies</p>
<p class="faq-answer abs" style="top:2200px">We decided to launch our service for two reasons: learning to trade is a difficult pro-cess that leaves many aspiring traders frustrated, and on top of that, there is short-age of bad signal services that take advantage of these traders.</p>
<div class="faq-rule abs" style="top:2303px"></div>
<p class="faq-q abs" style="top:2318px"><b>Q.</b>Tradlo.com works with both day as well as intraday traders.</p>
<div class="faq-rule abs" style="top:2361px"></div>
<p class="faq-q abs" style="top:2376px"><b>Q.</b>Tradlo.com works with both day as well as intraday traders.</p>
<div class="faq-rule abs" style="top:2419px"></div>
<a class="view-more abs">VIEW MORE <svg width="13" height="13" viewBox="0 0 13 13"><circle cx="6.5" cy="6.5" r="5.5" fill="none" stroke="var(--blue)" stroke-width="1.3"/><path d="M5.5 4 L8 6.5 L5.5 9" fill="none" stroke="var(--blue)" stroke-width="1.3"/></svg></a>

<h2 class="col-title abs" style="left:625px;top:2106px">About <span class="accent">Us</span></h2>
<p class="about-copy abs">Pardon my language but there is a lot of 'crap', on the internet, especially when it comes to the services I offer.&nbsp; I have spent countless hours and years of my life towards my passion for the currency industry.&nbsp; I finally developed a strategy I am proud of and stand by my prod-uct with my name and company brand.</p>
<ul class="about-list abs">
  <li><svg width="13" height="13" viewBox="0 0 13 13"><circle cx="6.5" cy="6.5" r="5.5" fill="none" stroke="var(--blue)" stroke-width="1.3"/><path d="M5.5 4 L8 6.5 L5.5 9" fill="none" stroke="var(--blue)" stroke-width="1.3"/></svg>We offer speedy, consistent, accurate and desired results.</li>
  <li><svg width="13" height="13" viewBox="0 0 13 13"><circle cx="6.5" cy="6.5" r="5.5" fill="none" stroke="var(--blue)" stroke-width="1.3"/><path d="M5.5 4 L8 6.5 L5.5 9" fill="none" stroke="var(--blue)" stroke-width="1.3"/></svg>We're a highly dependable and trusted forex trading platform.</li>
  <li><svg width="13" height="13" viewBox="0 0 13 13"><circle cx="6.5" cy="6.5" r="5.5" fill="none" stroke="var(--blue)" stroke-width="1.3"/><path d="M5.5 4 L8 6.5 L5.5 9" fill="none" stroke="var(--blue)" stroke-width="1.3"/></svg>Our motto is to 'Reshape Your Path' and also to ensure that you earn profits</li>
  <li><svg width="13" height="13" viewBox="0 0 13 13"><circle cx="6.5" cy="6.5" r="5.5" fill="none" stroke="var(--blue)" stroke-width="1.3"/><path d="M5.5 4 L8 6.5 L5.5 9" fill="none" stroke="var(--blue)" stroke-width="1.3"/></svg>Our objective is to provide global access to trusted forex signals.</li>
  <li><svg width="13" height="13" viewBox="0 0 13 13"><circle cx="6.5" cy="6.5" r="5.5" fill="none" stroke="var(--blue)" stroke-width="1.3"/><path d="M5.5 4 L8 6.5 L5.5 9" fill="none" stroke="var(--blue)" stroke-width="1.3"/></svg>Our services are highly affordable.</li>
</ul>

<section class="partners abs"></section>
<div class="partner-badge abs" style="left:87px"><span></span></div>
<div class="partner-badge abs" style="left:264px"><span></span></div>
<div class="partner-badge abs" style="left:441px"><span></span></div>
<div class="partner-badge abs" style="left:618px"><span></span></div>
<div class="partner-badge abs" style="left:795px"><span></span></div>
<div class="partner-badge abs" style="left:972px"><span></span></div>

<footer class="site-footer abs"></footer>
<div class="footer-brand abs"><span class="brand-dot"></span><span class="brand-name">Tradlo</span></div>
<h4 class="footer-heading abs" style="left:400px;top:2668px">CONTACT US</h4>
<ul class="contact-list abs">
  <li><svg width="13" height="13" viewBox="0 0 13 13"><path d="M3 1 L5 4 L4 5.5 C5 7.5 5.5 8 7.5 9 L9 8 L12 10 L10.5 12 C5 11.5 1.5 8 1 2.5Z" fill="#666"/></svg>(000)-555-0142 (Phone)</li>
  <li><svg width="13" height="13" viewBox="0 0 13 13"><rect x="3" y="1" width="7" height="4" fill="#666"/><rect x="1" y="5" width="11" height="5" rx="1" fill="#666"/><rect x="3" y="9" width="7" height="3" fill="#999"/></svg>(000)-555-0142 (Fax)</li>
  <li><svg width="13" height="13" viewBox="0 0 13 13"><rect x="1" y="3" width="11" height="8" fill="#666"/><path d="M1 3 L6.5 7.5 L12 3" fill="none" stroke="#fff" stroke-width="1"/></svg><a>www.tradlo.example</a></li>
  <li><svg width="13" height="13" viewBox="0 0 13 13"><path d="M6.5 12 C3 8 2.5 6.5 2.5 5 a4 4 0 0 1 8 0 c0 1.5 -.5 3 -4 7z" fill="#666"/><circle cx="6.5" cy="5" r="1.5" fill="#fff"/></svg>3350 Lorem Ipsum Dummy<br>Lorem Ipsum</li>
</ul>
<h4 class="footer-heading abs" style="left:653px;top:2668px">NEWSLETTER</h4>
<p class="newsletter-copy abs">Register Your Email address to get information about us</p>
<div class="email-field abs">Email Address</div>
<div class="subscribe-btn abs">SUBSCRIBE</div>
<h4 class="footer-heading abs" style="left:903px;top:2668px">FOLLOW US</h4>
<p class="follow-copy abs">Lorem ipsum dolor sit amet, conse ctetur adipiscing elit. Nulla in purus nibh. Donec ornare</p>
<div class="social-row abs"><span></span><span></span><span></span><span></span><span></span></div>
<div class="footer-rule abs"></div>
<p class="copyright abs">© Copyright 2017 Tradlo .All Rights Reserved</p>

</body>
</html>
```